Property Developer Business card design

we need a business card design + printing for a new Property developer company based in melbourne.
We are a group of investors investing in a property developer business. We have more projects involved in residential property as opposed to commercial property but we are involved in both market. we also provide consulting services with overseas investors willing to invest in the australian property market.
Updates
I have uploaded the logo. I'm not very convince with the colors of my logo... any suggestion please?.
Thanks guys!
Target Market(s)
property investors or person willing to purchase investment property
Industry/Entity Type
Residential
Contact Information for Business Card
Bramblecourt Holdings Australia Pty Ltd
Look and feel

```html
<!DOCTYPE html>
<html lang="en">
<head>
<meta charset="utf-8">
<title>Bramblecourt Holdings Australia – Business Card</title>
<link rel="stylesheet" href="https://fonts.googleapis.com/css2?family=Montserrat:wght@500;700&display=swap">
<style>
  :root {
    --backdrop: #3a2a20;
    --card: #ffffff;
    --card-shade: #ececec;
    --gold: #c9a23a;
    --brown: #5a1a10;
    --muted: #6b4a40;
  }
  * { box-sizing: border-box; margin: 0; padding: 0; }
  html, body { width: 1200px; height: 900px; overflow: hidden; }
  body {
    background: var(--backdrop);
    font-family: "Montserrat", Arial, sans-serif;
    position: relative;
  }
  .card {
    position: absolute;
    left: 320px;
    width: 560px;
    height: 320px;
    border-radius: 22px;
    background: radial-gradient(ellipse at 40% 35%, var(--card) 45%, var(--card-shade) 100%);
    box-shadow: 0 14px 30px rgba(0,0,0,.45);
    overflow: hidden;
  }
  .card--brand { top: 70px; }
  .card--contact { top: 510px; }

  .wordmark {
    display: flex;
    align-items: center;
    gap: 10px;
    font-weight: 700;
    color: var(--brown);
    line-height: 1.15;
  }
  .wordmark__square {
    width: 14px; height: 14px;
    background: var(--gold);
    flex: none;
  }
  .card--brand .wordmark {
    position: absolute;
    left: 44px;
    bottom: 60px;
    font-size: 19px;
  }
  .card--contact .wordmark {
    position: absolute;
    left: 40px;
    top: 118px;
    width: 210px;
    font-size: 18px;
  }

  .divider {
    position: absolute;
    left: 268px;
    top: 70px;
    width: 2px;
    height: 150px;
    background: var(--gold);
  }
  .person {
    position: absolute;
    left: 296px;
    top: 62px;
  }
  .person__name { font-weight: 700; font-size: 15px; color: var(--brown); }
  .person__role { font-weight: 500; font-size: 8px; color: var(--muted); margin-top: 3px; }

  .contact-list {
    position: absolute;
    left: 296px;
    top: 128px;
    right: 30px;
    list-style: none;
  }
  .contact-list li {
    display: flex;
    align-items: center;
    gap: 10px;
    font-size: 11px;
    font-weight: 500;
    color: var(--brown);
    margin-bottom: 8px;
    white-space: nowrap;
  }
  .contact-list svg { width: 11px; height: 11px; fill: var(--gold); flex: none; }

  .address {
    position: absolute;
    left: 190px;
    bottom: 40px;
    display: flex;
    align-items: center;
    gap: 8px;
    font-size: 12px;
    font-weight: 700;
    color: var(--brown);
  }
  .address svg { width: 11px; height: 15px; fill: var(--gold); }
</style>
</head>
<body>

<section class="card card--brand" aria-label="Card front">
  <div class="wordmark">
    <span class="wordmark__square"></span>
    <span>Bramblecourt Holdings<br>Australia</span>
  </div>
</section>

<section class="card card--contact" aria-label="Card back">
  <div class="wordmark">
    <span class="wordmark__square"></span>
    <span>Bramblecourt Holdings Australia</span>
  </div>

  <div class="divider"></div>

  <div class="person">
    <p class="person__name">Daniel Reyes</p>
    <p class="person__role">Managing Director</p>
  </div>

  <ul class="contact-list">
    <li>
      <svg viewBox="0 0 24 24"><path d="M6.6 10.8a15 15 0 0 0 6.6 6.6l2.2-2.2a1 1 0 0 1 1-.25 11.4 11.4 0 0 0 3.6.57 1 1 0 0 1 1 1V20a1 1 0 0 1-1 1A17 17 0 0 1 3 4a1 1 0 0 1 1-1h3.5a1 1 0 0 1 1 1c0 1.250.2 2.450.57 3.6a1 1 0 0 1-.25 1z"/></svg>
      +61 3 9000 4182
    </li>
    <li>
      <svg viewBox="0 0 24 24"><path d="M7 1h10a2 2 0 0 1 2 2v18a2 2 0 0 1-2 2H7a2 2 0 0 1-2-2V3a2 2 0 0 1 2-2zm0 3v14h10V4zm5 15.5a1.2 1.2 0 1 0 0 2.4 1.2 1.2 0 0 0 0-2.4z"/></svg>
      0400 555 318
    </li>
    <li>
      <svg viewBox="0 0 24 24"><path d="M12 2a10 10 0 1 0 5 18.7l-1-1.7A8 8 0 1 1 20 12v1a2 2 0 0 1-4 0V7h-2v1a5 5 0 1 0 .9 6.9A4 4 0 0 0 22 13v-1A10 10 0 0 0 12 2zm0 13a3 3 0 1 1 0-6 3 3 0 0 1 0 6z"/></svg>
      daniel@bramblecourt.com.au
    </li>
  </ul>

  <p class="address">
    <svg viewBox="0 0 16 22"><path d="M8 0a8 8 0 0 0-8 8c0 6 8 14 8 14s8-8 8-14a8 8 0 0 0-8-8zm0 11a3 3 0 1 1 0-6 3 3 0 0 1 0 6z"/></svg>
    14 Wattlebird Lane Hillside VIC 3037
  </p>
</section>

</body>
</html>
```